Webdesign für Verkauf von Stoffen
Zielgruppe
Plinzgarne ist schon seit 15 Jahren auf den Märkten unterwegs und verkauft seine hochwertigen Stoffe vor Ort. Nun muss die Webseite ein neuen Look bekommen, sie sollte modern und locker wirken. Die Webseite ist eher für Privatkunden und hat jetzt noch keine Shop Möglichkeit, die wird aber intrigiert mit einzelnen Produkten.
Aufgabenstellung
Logo gibt es noch nicht, soll erstmal nur in Schriftform bleiben, ansonsten gibt es keine explizierten Vorgaben

```html
<!DOCTYPE html>
<html lang="de">
<head>
<meta charset="utf-8">
<title>Plinz Garne – Feiner Zwirn</title>
<link rel="stylesheet" href="https://fonts.googleapis.com/css2?family=Inter:wght@300;400;500;600&display=swap">
<style>
:root{
  --brand:#8aa4d4;
  --ink:#333;
  --ink-soft:#555;
  --white:#fff;
  --tile:#000;
}
*{box-sizing:border-box;margin:0;padding:0}
html,body{width:1200px;height:3259px;overflow:hidden}
body{font-family:"Inter",sans-serif;color:var(--ink);background:var(--white);position:relative}
.topbar{height:42px;background:var(--brand);display:flex;justify-content:flex-end;align-items:center;gap:14px;padding-right:118px}
.topbar .social{font-size:13px;color:var(--white);font-weight:500}
.header{height:109px;display:flex;align-items:center;justify-content:space-between;padding:0 122px 0 87px}
.brand-name{font-size:20px;letter-spacing:2px;color:#555;line-height:1}
.brand-sub{font-size:14px;letter-spacing:2px;color:#555;margin-top:4px}
.nav{display:flex;gap:33px;margin-top:10px}
.nav a{font-size:14px;letter-spacing:1.6px;color:#555;text-decoration:none}
.hero{position:relative;height:412px;overflow:hidden}
.hero-photo{position:absolute;inset:0;background:linear-gradient(100deg,#8ea6d6 0%,#a3b4d8 40%,#c8c6c2 70%,#d9d3cc 100%)}
.hero-text{position:absolute;left:87px;top:64px;color:var(--white)}
.hero-text h1{font-size:37px;font-weight:600;line-height:45px;margin-bottom:22px;letter-spacing:-.5px}
.hero-text p{font-size:19px;font-weight:300;line-height:28px;letter-spacing:-.4px}
.claim{text-align:center;font-size:26px;font-weight:500;margin-top:40px;letter-spacing:-.3px;padding-left:90px}
.tiles{display:flex;gap:12px;margin:30px 0 0 100px}
.tile{width:157px;height:206px;background:var(--tile);color:var(--white);display:flex;align-items:center;justify-content:center;font-size:20px;font-weight:500;letter-spacing:-.3px}
.tile.light{background:var(--white);color:var(--ink);box-shadow:0 1px 5px rgba(0,0,0,.15)}
.sub-claim{text-align:center;font-size:26px;font-weight:500;margin-top:47px;letter-spacing:-.3px}
.fabrics{position:absolute;top:1003px;left:0;width:1200px}
.fabric-row{display:flex;height:338px}
.fabric-row.flip{flex-direction:row-reverse}
.fabric-photo{width:600px;height:100%}
.fabric-copy{width:600px;padding:24px 95px 0 31px}
.fabric-row.flip .fabric-copy{padding:38px 48px 0 87px}
.fabric-copy h2{font-size:27px;font-weight:500;margin-bottom:22px;letter-spacing:-.4px}
.fabric-copy p{font-size:17px;line-height:28px;color:var(--ink-soft);font-weight:400;letter-spacing:-.45px}
.contact{position:absolute;top:2432px;left:0;width:1200px;display:flex}
.map{width:600px;height:445px;background:linear-gradient(135deg,#eef0f2,#e3e6ea)}
.contact-form{padding:20px 0 0 31px;width:520px}
.contact-form h2{font-size:27px;font-weight:600;margin-bottom:8px}
.contact-form .lead{font-size:17px;line-height:25px;color:#444;margin-bottom:22px;letter-spacing:-.3px}
.field-row{display:flex;gap:18px}
label{display:block;font-size:16.5px;color:#333;margin-bottom:2px}
.input{border:1px solid #999;height:37px;margin-bottom:10px}
.input.area{height:108px}
.send{width:226px;height:38px;background:var(--brand);color:var(--white);font-size:17px;font-weight:600;border:none;font-family:inherit;display:block}
.footer{position:absolute;top:2956px;left:0;width:1200px;height:303px;background:var(--brand);color:var(--white)}
.footer-address{position:absolute;left:87px;top:36px;font-size:17.5px;line-height:25px;font-weight:300;letter-spacing:-.3px}
.footer-address strong{font-weight:600}
.footer-line{display:flex;align-items:center;gap:12px;margin-left:-35px;margin-top:3px}
.footer-line svg{width:23px;height:23px}
.footer-social{position:absolute;left:87px;top:222px;display:flex;gap:22px;font-size:16px;font-weight:500}
.footer-nav{position:absolute;left:461px;top:36px;display:flex;flex-direction:column;gap:20px;font-size:17.5px;font-weight:300}
.footer-legal{position:absolute;right:66px;top:257px;display:flex;gap:40px;font-size:17.5px;font-weight:300}
</style>
</head>
<body>
<div class="topbar">
  <span class="social">Profil</span><span class="social">Bilder</span><span class="social">Chat</span>
</div>
<header class="header">
  <div>
    <div class="brand-name">PLINZ GARNE</div>
    <div class="brand-sub">FEINER ZWIRN</div>
  </div>
  <nav class="nav"><a>HOME</a><a>PORTOFOLIO</a><a>ÜBER MICH</a><a>KONTAKT</a></nav>
</header>
<section class="hero">
  <div class="hero-photo" role="img" aria-label="Gerollte, bunt bedruckte Stoffballen, bläulich überlagert"></div>
  <div class="hero-text">
    <h1>Plinz Garne -<br>Feiner Zwirn</h1>
    <p>Ich biete derzeit auf dem Stoffmarkt Nordwind deutschlandweit<br>meine Stoffe an.<br>Der Onlineshop befindet sich momentan noch in der<br>Aufbauphase und ist voraussichtlich<br>ab Mitte 2022 für Euch zugänglich.</p>
  </div>
</section>
<h2 class="claim">Eleganz kommt nie aus der Mode</h2>
<div class="tiles">
  <div class="tile light">Gobelin</div>
  <div class="tile">Canvas</div>
  <div class="tile">Linen</div>
  <div class="tile">Sweat</div>
  <div class="tile">Jersey</div>
  <div class="tile">Musselin uvm.</div>
</div>
<h2 class="sub-claim">Bio Musselin 100% Baumwolle</h2>

<div class="fabrics">
  <div class="fabric-row">
    <div class="fabric-photo" role="img" aria-label="Gefaltete Leinen-Viskose-Stoffe in Orange, Rosa, Gelb und Petrol" style="background:linear-gradient(135deg,#d86a4a,#e7b7b9 35%,#d8b73a 55%,#6f9aa3 80%,#ddd6de)"></div>
    <div class="fabric-copy">
      <h2>Linen/Viskose</h2>
      <p>Lorem ipsum dolor sit amet, consetetur sadipscing elitr, sed diam nonumy eirmod tempor invidunt ut labore et dolore magna aliquyam erat, sed diam voluptua. At vero eos et accusam et justo duo dolores et ea rebum. Stet clita kasd gubergren, no sea takimata sanctus est Lorem ipsum dolor sit amet. Lorem ipsum dolor sit amet, consetetur sadipscing elitr, sed diam nonumy eirmod tempor invidunt ut labore</p>
    </div>
  </div>
  <div class="fabric-row flip">
    <div class="fabric-photo" role="img" aria-label="Stoffballen aus gewaschenem Leinen in Blau, Sand, Braun und Rot" style="background:linear-gradient(90deg,#3f9fbf,#3e6fc0 30%,#d8c784 50%,#9a5f44 65%,#c8243a 85%,#d8483e)"></div>
    <div class="fabric-copy">
      <h2>100% Linen Washed</h2>
      <p>Lorem ipsum dolor sit amet, consetetur sadipscing elitr, sed diam nonumy eirmod tempor invidunt ut labore et dolore magna aliquyam erat, sed diam voluptua. At vero eos et accusam et justo duo dolores et ea rebum. Stet clita kasd gubergren, no sea takimata sanctus est Lorem ipsum dolor sit amet. Lorem ipsum dolor sit amet, consetetur sadipscing elitr, sed diam nonumy eirmod tempor invidunt ut labore</p>
    </div>
  </div>
  <div class="fabric-row">
    <div class="fabric-photo" role="img" aria-label="Bio-Musselin-Ballen in Blau, Grün, Orange, Rot und Rosa" style="background:linear-gradient(100deg,#8fb3d6,#1f6f8c 25%,#2e5a3a 38%,#e48a1e 55%,#c21e2c 70%,#e6a39a 85%,#c9b9a0)"></div>
    <div class="fabric-copy">
      <h2>Bio Musselin</h2>
      <p>Lorem ipsum dolor sit amet, consetetur sadipscing elitr, sed diam nonumy eirmod tempor invidunt ut labore et dolore magna aliquyam erat, sed diam voluptua. At vero eos et accusam et justo duo dolores et ea rebum. Stet clita kasd gubergren, no sea takimata sanctus est Lorem ipsum dolor sit amet. Lorem ipsum dolor sit amet, consetetur sadipscing elitr, sed diam nonumy eirmod tempor invidunt ut labore</p>
    </div>
  </div>
  <div class="fabric-row flip">
    <div class="fabric-photo" role="img" aria-label="Sweat-Melange-Stoffe in Jeansblau, Gelb, Rost und Koralle" style="background:linear-gradient(90deg,#c2412c,#5f86b8 20%,#e9b752 40%,#e3cf3f 55%,#d7775a 75%,#d05a55)"></div>
    <div class="fabric-copy">
      <h2>Sweat Melange</h2>
      <p>Lorem ipsum dolor sit amet, consetetur sadipscing elitr, sed diam nonumy eirmod tempor invidunt ut labore et dolore magna aliquyam erat, sed diam voluptua. At vero eos et accusam et justo duo dolores et ea rebum. Stet clita kasd gubergren, no sea takimata sanctus est Lorem ipsum dolor sit amet. Lorem ipsum dolor sit amet, consetetur sadipscing elitr, sed diam nonumy eirmod tempor invidunt ut labore</p>
    </div>
  </div>
</div>

<section class="contact">
  <div class="map" role="img" aria-label="Stadtplan mit Standortmarkierung des Ateliers"></div>
  <div class="contact-form">
    <h2>Kontakt</h2>
    <p class="lead">Für Fragen und Buchungen melden Sie sich bei mir! Ich freue mich auf Ihre Nachricht.</p>
    <div class="field-row">
      <div style="width:226px"><label>Name</label><div class="input"></div></div>
      <div style="width:222px"><label>E-Mail-Adresse</label><div class="input"></div></div>
    </div>
    <label>Telefonnummer</label><div class="input" style="width:466px"></div>
    <label>Nachricht</label><div class="input area" style="width:466px"></div>
    <button class="send">Absenden</button>
  </div>
</section>

<footer class="footer">
  <div class="footer-address">
    <strong>Jonas Plinz</strong><br>
    Plinz Garne - Feiner Zwirn<br>
    Lindenhofweg 14<br>
    12049 Berlin
    <div class="footer-line"><svg viewBox="0 0 24 24" fill="none" stroke="#fff" stroke-width="1.5"><path d="M5 3h4l2 5-2.5 1.5a11 11 0 0 0 6 6L16 13l5 2v4a2 2 0 0 1-2 2A16 16 0 0 1 3 5a2 2 0 0 1 2-2z"/></svg>0176/10203040</div>
    <div class="footer-line"><svg viewBox="0 0 24 24" fill="none" stroke="#fff" stroke-width="1.5"><rect x="3" y="5" width="18" height="14"/><path d="M3 5l9 8 9-8"/></svg>post@plinzgarne.example</div>
  </div>
  <div class="footer-social"><span>Profil</span><span>Bilder</span><span>Chat</span></div>
  <nav class="footer-nav"><span>HOME</span><span>PORTOFOLIO</span><span>ÜBER MICH</span><span>KONTAKT</span></nav>
  <div class="footer-legal"><span>Impressum</span><span>Datenschutz</span><span>Cookie-Einstellungen</span></div>
</footer>
</body>
</html>
```